CONTEMPORARY Canva Art Design for Christians

I need a canvas art design on Christianity. The design must be in 3 SIMPLE dimensions: 12x 18 inches / 28 x 24 inches / 30 x 40 inches
The design must be accompanied by christian quote.
The christian quote can be "As For Me And My House We Will Serve The Lord (Joshua 24:15)" or any other quote that is good for display in a christian home.

I DON'T WANT THE TRADITIONAL CHRISTIAN DESIGN.. I WANT COLOURFUL, MEANINGFUL and CONTEMPORARY, MODERN DESIGN. And stay away from the scary image of Jesus in dark background, it only makes the home more scary not holy!

Target Market(s)

Christians

Colors

Designer to choose colors to be used in the design.

Requirements
Must have
• A graphic design and a christian quote that is powerful and edifies the soul. Great for display at home. Great use of colours to enhance the message.
Nice to have
• I wish to see great unique design with strong use of colours, images to enhance the scripture. It must glorify Jesus.
Should not have
• Should not be dull.

```html
<!DOCTYPE html>
<html lang="en">
<head>
<meta charset="utf-8">
<title>As For Me And My House – Canvas Art</title>
<link rel="stylesheet" href="https://fonts.googleapis.com/css2?family=Fredoka:wght@600;700&family=EB+Garamond:wght@500&display=swap">
<style>
  :root {
    --ink: #111111;
    --paper: #ffffff;
    --sun: #ffe12a;
    --amber: #ffb300;
    --orange: #f26a10;
    --red: #e5141d;
    --deep-red: #7a0a0e;
    --teal: #22b8b0;
    --sky: #3a8fe0;
    --violet: #7a3fc0;
    --magenta: #e0207a;
    --green: #9ed23a;
  }
  * { margin: 0; padding: 0; box-sizing: border-box; }
  html, body { width: 1200px; height: 750px; overflow: hidden; background: #f4f1ec; }

  .canvas-art {
    position: relative;
    width: 1200px;
    height: 750px;
    overflow: hidden;
    background:
      radial-gradient(ellipse 42% 46% at 56% 48%, rgba(255,255,255,0.95) 0%, rgba(255,255,255,0.7) 45%, rgba(255,255,255,0) 100%),
      radial-gradient(circle at 14% 10%, var(--sun) 0%, rgba(255,225,42,0) 40%),
      radial-gradient(circle at 88% 8%, #7fe0ff 0%, rgba(127,224,255,0) 30%),
      radial-gradient(circle at 4% 96%, var(--red) 0%, rgba(229,20,29,0) 38%),
      radial-gradient(circle at 96% 96%, var(--magenta) 0%, rgba(224,32,122,0) 40%),
      radial-gradient(circle at 100% 55%, var(--violet) 0%, rgba(122,63,192,0) 40%),
      linear-gradient(100deg, var(--amber) 0%, var(--green) 30%, var(--teal) 62%, var(--sky) 82%, var(--violet) 100%);
  }

  .cross { position: absolute; width: 40px; height: 40px; }
  .cross--left { left: 136px; top: 70px; }
  .cross--right { left: 1000px; top: 62px; }

  .shepherd-figure {
    position: absolute;
    left: 8px;
    top: 320px;
    width: 320px;
    height: 420px;
    border-radius: 48% 48% 10% 10% / 30% 30% 8% 8%;
    background: radial-gradient(ellipse 60% 70% at 50% 45%, #d9cbb4 0%, #b59a78 55%, rgba(150,110,70,0) 100%);
  }

  .quote-line {
    position: absolute;
    font-family: "Fredoka", sans-serif;
    font-weight: 700;
    line-height: 1;
    white-space: nowrap;
    letter-spacing: 1px;
  }
  .quote-line--dark {
    color: var(--ink);
    text-shadow: 3px 3px 0 var(--paper), -2px -2px 0 var(--paper), 2px -2px 0 var(--paper), -2px 2px 0 var(--paper);
  }
  .line-one { left: 321px; top: 74px; font-size: 128px; }
  .line-one .small { font-size: 96px; }

  .line-two {
    left: 211px; top: 196px; font-size: 137px;
    background: linear-gradient(180deg, var(--amber) 0%, var(--orange) 100%);
    -webkit-background-clip: text;
    background-clip: text;
    color: transparent;
    filter: drop-shadow(3px 3px 0 var(--ink));
  }
  .line-two .small { font-size: 108px; }

  .line-three { left: 359px; top: 366px; font-size: 120px; letter-spacing: 2px; }

  .line-four {
    left: 365px; top: 480px; font-size: 180px;
    color: var(--red);
    text-shadow: 4px 4px 0 var(--deep-red), -2px -2px 0 var(--paper);
  }
  .line-four .the { font-size: 134px; }
  .line-four .lord { font-size: 180px; letter-spacing: 0; margin-left: 40px; }

  .scripture-ref {
    position: absolute;
    left: 791px;
    top: 660px;
    font-family: "EB Garamond", serif;
    font-weight: 500;
    font-size: 32px;
    color: var(--paper);
    letter-spacing: 1px;
  }
</style>
</head>
<body>
  <main class="canvas-art">
    <svg class="cross cross--left" viewBox="0 0 40 40" aria-hidden="true">
      <path d="M20 4 V36 M8 14 H32" stroke="#c7a21a" stroke-width="3" fill="none"/>
    </svg>
    <svg class="cross cross--right" viewBox="0 0 40 40" aria-hidden="true">
      <path d="M20 4 V36 M8 14 H32" stroke="#2c7a50" stroke-width="3" fill="none"/>
    </svg>

    <div class="shepherd-figure" role="img" aria-label="Illustration of a shepherd in a white hooded robe holding a staff"></div>

    <p class="quote-line quote-line--dark line-one"><span class="small">As</span> For Me</p>
    <p class="quote-line line-two"><span class="small">And</span> My House</p>
    <p class="quote-line quote-line--dark line-three">We Will Serve</p>
    <p class="quote-line line-four"><span class="the">The</span><span class="lord">LORD.</span></p>
    <p class="scripture-ref">(JOSHUA 24:15)</p>
  </main>
</body>
</html>
```